Business Card Design for a Personal Trainer

I need a business card design for my job as a personal trainer. It should have a unique, modern and exclusive design. On the front there should be only my logo with my name and my job. 0162/3819204 Tobias Lendhart Wiesengrundweg 14 80417 Munich Germany The most important contact information is the web adress. it can be bigger than the rest, but its not necessary. The card should be 8,5cmx5,5cm big. Font: Roboto. Colors: black, white, gray, 56c1ff.

```html
<!DOCTYPE html>
<html lang="de">
<head>
<meta charset="utf-8">
<title>Tobias Lendhart – Personal Trainer Visitenkarte</title>
<link rel="stylesheet" href="https://fonts.googleapis.com/css2?family=Roboto:wght@400;500;700&display=swap">
<style>
  :root {
    --backdrop: #8b8b8b;
    --card: #2b2a2c;
    --brand: #56c1ff;
    --contact: #b4b4b4;
    --contact-strong: #c8c8c8;
    --photo-light: #58585a;
    --photo-dark: #2b2a2c;
  }
  * { margin: 0; padding: 0; box-sizing: border-box; }
  html, body {
    width: 1200px; height: 1200px; overflow: hidden;
    background: var(--backdrop);
    font-family: "Roboto", Arial, sans-serif;
  }
  .canvas { position: relative; width: 1200px; height: 1200px; }
  .card {
    position: absolute; left: 220px; width: 761px; height: 492px;
    background: var(--card);
  }
  .card--front { top: 92px; }
  .card--back { top: 618px; }

  .brand {
    position: absolute; left: 0; right: 0; top: 296px;
    text-align: center; color: var(--brand);
  }
  .brand__mark {
    position: absolute; left: 50%; top: -140px;
    width: 60px; height: 60px; margin-left: -30px;
    background: var(--brand);
  }
  .brand__name {
    display: block; font-size: 66px; font-weight: 400;
    line-height: 1; letter-spacing: 0.01em;
  }
  .brand__role {
    display: flex; align-items: center; justify-content: center;
    margin-top: 8px; gap: 10px;
  }
  .brand__rule { width: 84px; height: 2px; background: var(--brand); }
  .brand__role-text {
    font-size: 26px; letter-spacing: 0.3em; line-height: 1;
    margin-right: -0.3em;
  }

  .portrait {
    position: absolute; left: 44px; top: 50px; width: 260px; height: 442px;
    background: radial-gradient(ellipse 70% 60% at 50% 50%, var(--photo-light), var(--photo-dark) 100%);
  }
  .contact {
    position: absolute; left: 331px; top: 186px;
    list-style: none; color: var(--contact);
    font-size: 21px; letter-spacing: 0.2em; line-height: 37.6px;
  }
  .contact__web {
    color: var(--contact-strong); font-weight: 700;
    font-size: 22px; letter-spacing: 0.26em;
  }
</style>
</head>
<body>
<main class="canvas">
  <section class="card card--front" aria-label="Vorderseite">
    <div class="brand">
      <span class="brand__mark" aria-hidden="true"></span>
      <span class="brand__name">TOBIAS LENDHART</span>
      <span class="brand__role">
        <span class="brand__rule"></span>
        <span class="brand__role-text">PERSONAL TRAINER</span>
        <span class="brand__rule"></span>
      </span>
    </div>
  </section>

  <section class="card card--back" aria-label="Rückseite">
    <div class="portrait" role="img" aria-label="Schwarz-Weiß-Porträt des Trainers mit verschränkten Armen"></div>
    <ul class="contact">
      <li class="contact__web">www.tobiaslendhart.de</li>
      <li>t.lendhart@mailpost.de</li>
      <li>0162/3819204</li>
      <li>Tobias Lendhart</li>
      <li>Wiesengrundweg 14</li>
      <li>80417 München</li>
    </ul>
  </section>
</main>
</body>
</html>
```